Corporate Business Card

Very professional, Modern, Not to busy, include phone address email, website
(253) 617-4930, 18761 52nd Avenue S, Kent, WA 98047, martin@plumlinegroup.com, varkoworks.com

Target Market(s)

Manufacturing

Industry/Entity Type

Aero, machining, manufacturing, Off road racing

Contact Information for Business Card

Phone, address email, website

```html
<!DOCTYPE html>
<html lang="en">
<head>
<meta charset="utf-8">
<title>Varko Works – Business Card</title>
<link rel="stylesheet" href="https://fonts.googleapis.com/css2?family=Orbitron:wght@700&family=Roboto:wght@400;500&display=swap">
<style>
  :root {
    --page-bg: #2c2c2d;
    --front-top: #1b1c1e;
    --front-bottom: #2b2c2f;
    --back-top: #2b3b6a;
    --back-bottom: #25335f;
    --text-light: #e9ebf0;
    --accent-red: #c8222a;
    --wordmark-grey: #56585d;
  }
  * { margin: 0; padding: 0; box-sizing: border-box; }
  html, body {
    width: 1200px; height: 1138px; overflow: hidden;
    background: var(--page-bg);
    font-family: "Roboto", Arial, sans-serif;
  }
  .card {
    position: absolute;
    border-radius: 14px;
    box-shadow: 0 6px 14px rgba(0,0,0,0.45);
  }
  .card-front {
    left: 274px; top: 186px; width: 624px; height: 376px;
    background: linear-gradient(160deg, var(--front-top) 0%, var(--front-top) 40%, var(--front-bottom) 100%);
  }
  .card-back {
    left: 276px; top: 608px; width: 618px; height: 374px;
    background: linear-gradient(180deg, var(--back-top) 0%, var(--back-bottom) 100%);
  }
  .wordmark {
    position: absolute; left: 0; right: 0; top: 118px;
    text-align: center;
    font-family: "Roboto", Arial, sans-serif;
    font-weight: 500; font-size: 52px; letter-spacing: 6px;
    color: var(--wordmark-grey);
  }
  .front-url {
    position: absolute; left: 0; right: 0; top: 328px;
    text-align: center;
    font-size: 16px; letter-spacing: 10.5px;
    color: var(--text-light);
  }
  .front-url .accent { color: var(--accent-red); }
  .contact {
    position: absolute; left: 0; right: 0; top: 112px;
    text-align: center; color: var(--text-light);
  }
  .contact-name {
    font-family: "Orbitron", "Arial Black", sans-serif;
    font-weight: 700; font-size: 28px; letter-spacing: 0.5px;
    line-height: 32px; margin-bottom: 12px;
  }
  .contact-name .surname { color: var(--accent-red); }
  .contact-line { font-size: 17px; line-height: 24px; }
  .contact-address { margin-top: 9px; }
</style>
</head>
<body>
  <section class="card card-front">
    <div class="wordmark">VARKO WORKS</div>
    <div class="front-url">www.varko<span class="accent">works</span>.com</div>
  </section>

  <section class="card card-back">
    <div class="contact">
      <h1 class="contact-name">MARTIN <span class="surname">HALE</span></h1>
      <p class="contact-line">(253) 617-4930</p>
      <p class="contact-line">martin@plumlinegroup.com</p>
      <p class="contact-line">www.varkoworks.com</p>
      <p class="contact-line contact-address">18761 52nd Avenue S, Kent, WA 98047</p>
    </div>
  </section>
</body>
</html>
```